Diverse, up-scale salon needs eye-catching, unique business cards.

We are looking for a unique business card design for our stylist but that can also be multi functional and used for appointment reminder and referrals. I will need a design in a format that I can modify names and titles going forward. In the past we have had a dark background with the logo on one side, and stylist and contact information on the other but we are open to all ideas. I have included our mission statement as well as branded colors below. The statement doesn't need to go on the card, it's just a reference for target market. We need space for the stylists name, title, instagram handle and then the salons phone number, website and address. I am also open to adding a spot for a qr code linked to the stylist instagram or the salon booking link.

primary brand colors:
#333333 #233415 #36502a #93874a #000000
Mission statement:
Vessolin Hair Studio, a high-end salon located in the lively Downtown Farmington, Michigan, is committed to providing exceptional services in a welcoming and relaxed environment to meet the needs of our diverse clientele.
Our salon specializes in contemporary custom haircuts, coloring, extensions, and barbering and beard grooming services. Our team of skilled stylists is passionate and inventive in their hair styling techniques. At the heart of our salon are values centered on quality, innovation, creativity, and above all, comfort. These core values are evident in every appointment across our customizable array of services.
Our goal is to establish a benchmark for exceptional hair care for every human.
Website: www.vessolinhairstudio.example
instagram: @vessolinhairstudio
address: 41782 Pelham Crest Rd, Farmington MI
phone: 248-613-4087

Industry/Entity Type

Hair Salon

Contact Information for Business Card

Stylist name, title, phone, instagram, website, address, (optional qr code)

Requirements
Should not have
• Does not need mission statement on the card.

```html
<!DOCTYPE html>
<html lang="en">
<head>
<meta charset="utf-8">
<title>Vessolin Hair Studio – Round Business Card</title>
<link rel="stylesheet" href="https://fonts.googleapis.com/css2?family=Poppins:wght@400;600&display=swap">
<style>
  :root {
    --backdrop: #5c5c5c;
    --card-light: #eeeeee;
    --card-dark: #231f20;
    --gold: #93874a;
    --ink: #111111;
  }
  html, body {
    margin: 0;
    padding: 0;
    width: 1200px;
    height: 900px;
    overflow: hidden;
    background: var(--backdrop);
  }
  .canvas {
    position: relative;
    width: 1200px;
    height: 900px;
    font-family: "Poppins", sans-serif;
  }
  .card {
    position: absolute;
    top: 234px;
    width: 416px;
    height: 416px;
    border-radius: 50%;
    box-sizing: border-box;
  }
  .card-front {
    left: 183px;
    background: var(--card-light);
    color: var(--ink);
    text-align: center;
  }
  .card-back {
    left: 623px;
    background: var(--card-dark);
    display: flex;
    align-items: center;
    justify-content: center;
  }
  .stylist-name {
    position: absolute;
    top: 64px;
    left: 0;
    right: 0;
    margin: 0;
    font-size: 22px;
    font-weight: 600;
    color: var(--gold);
    letter-spacing: 0.3px;
    line-height: 30px;
  }
  .stylist-title {
    position: absolute;
    top: 90px;
    left: 0;
    right: 0;
    margin: 0;
    font-size: 19px;
    font-weight: 400;
    line-height: 26px;
  }
  .divider {
    position: absolute;
    left: 180px;
    width: 56px;
    height: 1px;
    background: var(--gold);
  }
  .divider-1 { top: 133px; }
  .divider-2 { top: 218px; }
  .divider-3 { top: 297px; }
  .info-block {
    position: absolute;
    left: 0;
    right: 0;
    margin: 0;
    font-size: 18.5px;
    font-weight: 400;
    line-height: 25px;
    font-style: normal;
  }
  .address { top: 151px; }
  .contact { top: 234px; }
  .social {
    position: absolute;
    top: 322px;
    left: 0;
    right: 0;
    display: flex;
    align-items: center;
    justify-content: center;
    gap: 8px;
    font-size: 18.5px;
  }
  .social-dot {
    width: 18px;
    height: 18px;
    border-radius: 50%;
    background: var(--gold);
  }
  .brand-name {
    margin: 0;
    font-size: 28px;
    font-weight: 600;
    color: var(--gold);
    letter-spacing: 1px;
    text-align: center;
    line-height: 38px;
  }
</style>
</head>
<body>
  <div class="canvas">
    <section class="card card-front" aria-label="Card front with stylist details">
      <h1 class="stylist-name">MARCUS DELANO</h1>
      <p class="stylist-title">Managing Director</p>
      <div class="divider divider-1"></div>
      <address class="info-block address">41782 Pelham Crest Rd,<br>Farmington MI</address>
      <div class="divider divider-2"></div>
      <p class="info-block contact">248-613-4087<br>www.vessolinhairstudio.example</p>
      <div class="divider divider-3"></div>
      <p class="social" style="margin:0"><span class="social-dot"></span>@vessolinhairstudio</p>
    </section>

    <section class="card card-back" aria-label="Card back with studio name">
      <p class="brand-name">Vessolin<br>Hair Studio</p>
    </section>
  </div>
</body>
</html>
```